Stage Design Company Business Card

We are looking to step up up our business card design for our team.

We are a Full service Design and Consultation company for Stage and TV with an emphasis in Theatrical Lighting.

We like our materials to be clean and modern with solid colors free of patterns and gradients. Our brand consists of 4 primary colors Purple, Black, Grey, and White. Provided is our Word Mark as well as our Symbol Logo.

We would like our cards to leave an impression beyond the information, show our attention to design and detail, and make our marks an easily recognized feature (together or apart) for our clients.

We need a warm approachable comfortable feel for some clients, and a professional flair for the board member type clients.

Attached are our brand elements, and our existing cards to give a sense of our style and a glipse at the information we provide on our cards.

Target Market(s)

broad client base from church leaders to high school teachers and architects.

Industry/Entity Type

Business

Contact Information for Business Card

We format our phone number with periods not parenthesis or dashes. Information will be edited for each of our team members, and team member specific cards are not part of this scope, but rather a template so to speak.

Font styles to use
Sans Serif

Colors
6b449b
ffffff
000000
333333
aaaaaa

Requirements
Must have
• Wordmark and logo mark present (does not need to exist on the same side of card)
• Brand Colors,
• Name, Phone, Email, Address.
• Unique choices that make someone stop and take a second look
Nice to have
• It would be nice to somehow convey what we DO, as our brand name does not lend itself to this, outside of an obvious tagline though.....
• social media if not crowded. all of our handles match (instagram, twitter, facebook)
Should not have
• "clipart"

```html
<!DOCTYPE html>
<html lang="en">
<head>
<meta charset="utf-8">
<title>Corvane Stagecraft Business Card</title>
<link href="https://fonts.googleapis.com/css2?family=Source+Sans+3:wght@300;400;600;700&display=swap" rel="stylesheet">
<style>
  :root {
    --stage-bg: #5f5f5f;
    --card-white: #ffffff;
    --brand-purple: #33006b;
    --ink: #111111;
    --ink-soft: #555555;
    --grey-light: #aaaaaa;
    --font-main: "Source Sans 3", Arial, sans-serif;
  }
  * { margin: 0; padding: 0; box-sizing: border-box; }
  html, body { width: 1200px; height: 1200px; overflow: hidden; }
  body { background: var(--stage-bg); font-family: var(--font-main); position: relative; }

  .card {
    position: absolute;
    left: 120px;
    width: 960px;
    height: 540px;
    border-radius: 34px;
    overflow: hidden;
  }
  .card--front { top: 50px; background: var(--card-white); color: var(--ink); }
  .card--back { top: 610px; background: var(--brand-purple); color: var(--card-white); }

  /* Front: person */
  .person { position: absolute; left: 68px; top: 50px; }
  .person__name { font-size: 46px; font-weight: 600; letter-spacing: -0.5px; line-height: 1; color: var(--ink); }
  .person__title { font-size: 26px; font-weight: 300; color: var(--ink-soft); margin-top: 4px; }

  .contact-list { position: absolute; left: 68px; top: 182px; list-style: none; }
  .contact-list li { display: flex; align-items: center; height: 37px; font-size: 29px; font-weight: 400; }
  .contact-list svg { width: 26px; height: 26px; margin-right: 14px; flex: none; }

  .office { position: absolute; left: 70px; top: 374px; }
  .office__company { font-size: 26px; font-weight: 600; color: var(--brand-purple); margin-bottom: 6px; }
  .office__line { font-size: 29px; line-height: 38px; }

  /* Wordmark */
  .wordmark { position: absolute; text-align: left; white-space: nowrap; }
  .wordmark__name { font-weight: 700; line-height: 1; }
  .wordmark__sub { font-weight: 700; line-height: 1; }

  .card--front .wordmark { left: 512px; top: 58px; }
  .card--front .wordmark__name { font-size: 60px; letter-spacing: 22px; color: var(--ink); }
  .card--front .wordmark__sub { font-size: 15px; letter-spacing: 14.5px; color: var(--grey-light); margin-top: 20px; }

  /* Back */
  .brand-dot {
    position: absolute; left: 110px; top: 148px;
    width: 176px; height: 176px; border-radius: 50%;
    border: 6px solid var(--card-white);
  }
  .card--back .wordmark { left: 336px; top: 176px; }
  .card--back .wordmark__name { font-size: 64px; letter-spacing: 24px; color: var(--card-white); }
  .card--back .wordmark__sub { font-size: 16px; letter-spacing: 15.5px; color: var(--card-white); margin-top: 24px; }

  .connect { position: absolute; left: 336px; top: 398px; width: 520px; }
  .connect__label { display: flex; align-items: center; font-size: 13px; letter-spacing: 3px; font-weight: 600; }
  .connect__rule { flex: 1; height: 1.5px; background: var(--grey-light); margin-left: 18px; opacity: 0.8; }
  .connect__handle { font-size: 29px; font-weight: 400; margin-top: 22px; }
</style>
</head>
<body>

<section class="card card--front" aria-label="Card front">
  <div class="person">
    <div class="person__name">Mara L Quinlan</div>
    <div class="person__title">Job Title</div>
  </div>

  <ul class="contact-list">
    <li>
      <svg viewBox="0 0 24 24" aria-hidden="true"><rect x="6" y="2" width="12" height="20" rx="2" fill="none" stroke="#33006b" stroke-width="2.4"/><line x1="10" y1="18.5" x2="14" y2="18.5" stroke="#33006b" stroke-width="2"/></svg>
      000.000.0000
    </li>
    <li>
      <svg viewBox="0 0 24 24" aria-hidden="true"><path d="M7 2c1 0 2 3 2.5 4.5.3 1-1.5 2-1.5 2.5 0 2 3 7 5 8 .6.2 1.6-1.6 2.4-1.4 1.5.4 4 2 3.6 3-.6 1.7-2.3 3-4 3C9 21 4 12 4 6c0-2 1.5-4 3-4z" fill="#33006b"/></svg>
      555.014.2830
    </li>
    <li>
      <svg viewBox="0 0 24 24" aria-hidden="true"><rect x="2" y="6" width="20" height="13" fill="#33006b"/><polyline points="2,6 12,14 22,6" fill="none" stroke="#ffffff" stroke-width="1.6"/></svg>
      mara@corvane-sc.com
    </li>
    <li>
      <svg viewBox="0 0 24 24" aria-hidden="true"><g fill="none" stroke="#33006b" stroke-width="1.6"><circle cx="12" cy="12" r="9.5"/><ellipse cx="12" cy="12" rx="4.5" ry="9.5"/><line x1="2.5" y1="12" x2="21.5" y2="12"/><line x1="4" y1="7.5" x2="20" y2="7.5"/><line x1="4" y1="16.5" x2="20" y2="16.5"/></g></svg>
      corvane-sc.com
    </li>
  </ul>

  <div class="office">
    <div class="office__company">Corvane Stagecraft</div>
    <div class="office__line">19 N Harbor Ave</div>
    <div class="office__line">Linden, OR 97410</div>
  </div>

  <div class="wordmark">
    <div class="wordmark__name">CORVANE</div>
    <div class="wordmark__sub">STAGECRAFT</div>
  </div>
</section>

<section class="card card--back" aria-label="Card back">
  <div class="brand-dot" aria-hidden="true"></div>
  <div class="wordmark">
    <div class="wordmark__name">CORVANE</div>
    <div class="wordmark__sub">STAGECRAFT</div>
  </div>
  <div class="connect">
    <div class="connect__label">LET'S CONNECT<span class="connect__rule"></span></div>
    <div class="connect__handle">@corvanestage</div>
  </div>
</section>

</body>
</html>
```